Ecological Cosmetics (w/ Social Impact) Website

Dr. Wendelin Marovitz Naturprodukte KELVORA®, a small family-run ecological cosmetics “start-up” business (has been around since the mid 90s but only now beginning professionalize management), wishes to redesign its web presence, as part of a comprehensive “facelift” that will also encompass at a later stage its corporate identity (e.g. logo…).
We would like to prepare a new trilingual (later 3 additional languages will be added) website (www.kelvora7.at) that is symbiotic with web 2.0 enabled interwoven with a blog, news section, social networks integrated (e.g. preference/like buttons, Facebook), changing images and announcements appearing on first page, online payment services, mobile internet compatibility (e.g. iOS, Android, BlackBerry… thus no use of Flash, no need for a specific app), etc. and all the other significant trends in the e-commerce realm. The website should be easily and quickly accessible, fun to navigate, allow us to update it simply (through a content manager) and so “sexy” that people will want to return to the web, inform themselves of events and news, and hopefully also try our products.
Our company is based in Austria and specializes in the production of organic cosmetics in the mid-upper pricing range. We pride ourselves in offering natural cosmetics (the meaning of “natural” is relative and each person may have a different definition), with no petrochemical preservatives. Some of our products, such as the mineral salts and black mud powder from the Dead Sea cannot be obtained more naturally, unless you actually visit the area, thus retain all their properties. Our products are not medicine but the basic Dead Sea ingredients are used by spas and clinics in the area to treat many different skin, joint and bone affections. Our male and female customers (no distinction made will be made on our new website), primarily as of the ages of 25 to 65, buy KELVORA® because they:
• Care about the exterior and interior well-being
• Wish to look well cared, preserve their skin’s flexibility, natural splendor & properties
• Prefer natural skin care
• Nourish their skin with vital minerals/trace elements, protecting/treating their skin with natural ingredients
• Willing to pay more than average for natural cosmetics, looking for quality,
• Don’t mind spending about 15 minutes per week preparing a mud mask with some hot water.
• Bathe in water enriched with mineral salts
• Know or are surprised to find out that Dead Sea mud is one of the few, if not the only, naturally astringent (tenses the skin) muds in the world
• Help alleviate skin conditions (e.g. psoriasis, dermatitis, acne, eczema, pustules, oily skin ...), joint (e.g. rheumatism, arthritis ...) and cardiovascular disease.
Amongst the minerals in many of our products (particularly salt, mud), are sulfur and zinc, two naturally disinfecting and healing minerals, thus their common use in many dermatological drugs. Both salt and mud powder are completely natural, and without chemicals additives, quite important when dealing with sensitive or problematic skin, which reacts allergically to certain types of substances. The KELVORA line blends in both ingredients, enriching them with the highest-quality vitamins, essential oils and exceptional plant oils. Many of the competitors creams today use common ingredients such as petrolatum, paraffin (paraffinum liquidum), mineral oil, among others, which are derived from oil, are cheap ingredients (higher margins!) and clog pores!
To underline that this is not a chimera, there are quite a few researchers/scientists/doctors who have written articles about the benefits of the Dead Sea and its naturally occurring substances. Below are some links to abstracts of research papers, which are helpful in understanding the therapeutic potential of the black mud powder and mineral salt:
http://onlinelibrary.wiley.com/doi/10.1111/j.1365-4362.1995.tb03599.x/abstract
http://onlinelibrary.wiley.com/doi/10.1111/j.1365-4632.2005.02079.x/full
http://onlinelibrary.wiley.com/doi/10.1046/j.1365-4362.1997.00204.x/abstract
http://ard.bmj.com/content/49/2/99.short
http://www.springerlink.com/content/pv46n2p1m9p3k131/
http://onlinelibrary.wiley.com/doi/10.1111/j.1365-4632.2005.02621.x/full
http://journals.lww.com/jclinrheum/Abstract/2002/08000/Therapy_With_Mud_Compresses_for_Knee.3.aspx
http://onlinelibrary.wiley.com/doi/10.1111/j.1468-3083.1997.tb00509.x/abstract
http://onlinelibrary.wiley.com/doi/10.1046/j.1529-8019.2003.01622.x/full
http://onlinelibrary.wiley.com/doi/10.1046/j.1365-4362.1999.00583.x/full
The following links lead you to KELVORA® product data, mineral characteristics and a video of how to prepare a facial mud mask:
http://www.kelvora7.at/descargaanalisis.htm
http://www.kelvora7.at/estudio.htm
http://www.clipverse.example/watch?v=Qm4TzLp8WxR
We would like to convey, through our striking and attractive new graphic design, our values to potential clients: quality, 100% natural product, effectiveness, seriousness, confidence, respect for the environment, people, animals (the products are not tested on animals), all of which has a price (they are not cheap!). To put our money where our mouth is and contribute to transforming our planet into a better place, we are discussing with NGOs donating a percentage of certain product sales to support their causes.
Our web currently is available in 3 languages: German, Spanish and English, however, we plan to expand it by another 2 to 3 languages (Portuguese, Russian, Chinese). We are looking for a graphic design that will communicate our values and captivate people's attention, thereby helping us increase sales, projecting a solid and elegant image of reliability, effectiveness, simplicity and trust. Although we are not, and do not wish to, market our products as medicine, we do want to express, through our new graphic design, the fact that these products can be used to treat all types of skin, mitigate certain skin affections (e.g. psoriasis, dermatitis, acne, eczema, sensitive skin), and, depending on each organism’s reaction, different ailments (e.g. arthritis, rheumatism), although they won’t cure them (they can alleviate!).
To get an idea of our company, I invite you to explore our website, www.kelvora7.at, and see photos of our products. Attached please find some photos of our products, including the newly designed black mud powder box. We would like to create a unified corporate image. At this point we know that some, if not all, packages do not convey quality nor our values – this is something we wish to gradually change as each products’ graphic design and packaging gets renewed, consistent with the new brand image. This is work-in-progress and will be addressed as the company grows and has the financial capacity to invest in new design and packaging. We are advancing step by step.
Content-wise, we would provide you with product photos, and the texts to be inserted, but would like to complement these with other photos (e.g. from photobanks that include images of the Dead Sea, beaches, plants, nature…). The design should quickly associate the Internet user/visitor of our website with our values and the idea of quality products. A content manager will be used to update and modify our product portfolio.
Although some people will find us by typing into their web browser the address of our website, many will use search engines to locate us on the WWW. For this purpose, it would also be important that kelvora7.at’s different webpages can be referenced, searched for keywords and allow analysis of webtraffic (e.g. Google Analytics…).
Two colors are being used in our packages, green Pantone No. 326 and blue Pantone No. 072. We are completely flexible in terms of colors.
We hope you find the project interesting. Any questions, please do not hesitate to contact us. Thank you very much for your time, recommendations and proposals. Ideally we can close this project in about 14 days.
Information to be considered and/or included in the design:
• The web will feature an e-commerce shop, whose design should also be included in your creative proposal.
• Cosmetics tend to be divided along the lines of skin types, yet as the KELVORA line is still quite small, we have decided to divide it along treatment areas: hair, face, body. Each product is indicated for a particular skin type.
• Keyword Search box for the entire website
The current web is slow, all in Flash, difficult to navigate, has too many intermediate stages, does not offer a keyword search function, nor incorporate any web 2.0 features. Furthermore, it is more difficult to find and index in search engines as none of the pages have specific web addresses. In terms of intermediate pages, these should be eliminated shortening the time the user needs to obtain the desired information (e.g. the landing page where you choose sex & language, followed by drop of water being filled up), such that the visitor is directly lead to the main page (equal to the landing page). At first glance, the blue background and the drop of water filling up may lead the visitor to believe we are dedicated to something with water, perhaps even plumbing or purification services – such an impression must be avoided. Perhaps one of the ways to analyze all the aspects to be incorporated is an evaluation of our current web’s weaknesses and prepare a design where those are all addressed.
Target Market(s)
Male & female customers, approx. age 18-65, who care about their exterior and interior well being, “worried” about their skin, willing to pay more tha
Industry/Entity Type
Graphic Design
Requirements
Must have
- • The web will also feature a blog and an e-commerce shop, whose designs should also be included in your creative proposal.
• Address current and future languages
Content-wise, we will product photos, and the texts to be inserted, but would like to complement these with other photos (e.g. from photobanks that include images of the Dead Sea, beaches, plants, nature…). The design should quickly associate the Internet user/visitor of our website with our values and the idea of quality products. A content manager will be used to update and modify our product portfolio, as well as effects announcements on the landing page.

```html
<!DOCTYPE html>
<html lang="en">
<head>
<meta charset="utf-8">
<title>KELVORA Naturprodukte</title>
<link rel="stylesheet" href="https://fonts.googleapis.com/css2?family=PT+Sans:wght@400;700&family=Crimson+Text:wght@400;600&display=swap">
<style>
:root{
  --sky-top:#2aa3ea;
  --sky-mid:#6cc4f2;
  --sea:#1478c4;
  --brand:#1a63ad;
  --brand-dark:#0b4f97;
  --text:#1e6db0;
  --muted:#8a96a3;
  --nav-a:#1f76c8;
  --nav-b:#0d58a6;
  --panel:#eef5fa;
  --read:#cfe4f1;
  --footer:#0b5e97;
  --white:#ffffff;
  --line:#d5dde4;
}
*{margin:0;padding:0;box-sizing:border-box}
html,body{width:1061px;height:1200px;overflow:hidden}
body{position:relative;background:var(--white);font-family:"PT Sans",Arial,sans-serif;color:var(--text)}
.abs{position:absolute}

/* header */
.hero{left:0;top:0;width:1061px;height:528px;background:linear-gradient(180deg,var(--sky-top) 0%,var(--sky-mid) 40%,#8fd0f2 55%,var(--sea) 70%,#1f8bd2 100%)}
.hero-rule{left:0;top:523px;width:1061px;height:5px;background:#86cdf1}
.logo{left:49px;top:24px;width:124px;height:124px;border-radius:50%;background:var(--white);border:4px solid #dfe9f2;display:flex;align-items:center;justify-content:center;font-size:18px;font-weight:700;color:var(--brand-dark)}
.lang-label{left:731px;top:20px;font-size:14px;color:var(--brand)}
.lang{top:10px;width:40px;height:30px;background:var(--white);border-radius:0 0 4px 4px;font-size:17px;color:var(--brand);display:flex;align-items:center;justify-content:center}
.social-box{left:866px;top:62px;width:126px;height:32px;background:var(--white);border-radius:4px;display:flex;gap:8px;align-items:center;justify-content:center}
.social{width:21px;height:21px;border-radius:4px}
.s-a{background:#3b5998}.s-b{background:#2fa8e0}.s-c{background:#c4302b}.s-rss{background:#f27a1a}

.nav{left:333px;top:108px;width:675px;height:48px;background:linear-gradient(180deg,var(--nav-a),var(--nav-b));border-radius:4px;display:flex;list-style:none;box-shadow:0 2px 4px rgba(0,0,0,.2)}
.nav li{height:48px;display:flex;align-items:center;justify-content:center;font-size:14px;color:var(--white);border-right:1px solid rgba(255,255,255,.18)}
.nav li:last-child{border-right:none}
.nav .active{background:var(--brand-dark);border-radius:4px 0 0 4px}

/* slider */
.slider-frame{left:31px;top:166px;width:984px;height:321px;background:rgba(255,255,255,.35);box-shadow:0 6px 10px rgba(0,40,90,.3)}
.slider{left:36px;top:172px;width:974px;height:311px;background:linear-gradient(90deg,#e7edf2,#ffffff 60%);overflow:hidden}
.slide-title{left:49px;top:52px;font-family:"Crimson Text",Georgia,serif;font-size:27px;color:var(--brand)}
.slide-title b{font-weight:600}
.slide-title span{font-weight:400}
.slide-copy{left:52px;top:90px;width:340px;font-size:11.5px;line-height:20.7px;color:var(--brand)}
.slide-btn{left:50px;top:188px;width:175px;height:25px;background:#2b73bb;border-radius:3px;color:var(--white);font-size:11.5px;display:flex;align-items:center;justify-content:center}
.dots{left:52px;top:253px;display:flex;gap:5px}
.dot{width:31px;height:31px;border-radius:50%;background:#cde1ef;color:#3d7fb9;font-size:18px;display:flex;align-items:center;justify-content:center}
.dot.on{background:#2473be;color:var(--white)}
.slide-photo{left:518px;top:0;width:456px;height:311px}
.slide-arrow{left:497px;top:124px;width:38px;height:38px;border-radius:50%;background:#eef4f9;border:1px solid #9ab9d6;display:flex;align-items:center;justify-content:center}

/* content */
.h2{font-size:19px;font-weight:400;color:var(--brand)}
.welcome-h{left:27px;top:573px}
.welcome-copy{left:26px;top:606px;width:718px;font-size:11.5px;line-height:15.6px;color:var(--text)}
.welcome-copy p+p{margin-top:7px}
.welcome-copy p.tight{margin-top:0}
.latest-h{left:26px;top:773px}
.card{top:807px;width:228px;height:239px;border:1px solid var(--line);border-radius:5px;background:var(--white)}
.card .thumb{position:absolute;left:7px;top:13px;width:212px;height:114px}
.card .name{position:absolute;left:12px;top:131px;font-size:15px;color:var(--brand)}
.card .desc{position:absolute;left:11px;top:157px;width:208px;font-size:11px;line-height:15px;color:var(--text)}
.card .more{position:absolute;left:12px;top:210px;font-size:11px;color:#333}

.news-h{left:761px;top:558px}
.news{left:763px;width:262px;border-left:3px solid #3d83c2;padding-left:12px}
.news .date{font-size:12.5px;color:var(--brand)}
.news .copy{margin-top:3px;font-size:11.5px;line-height:15.5px;color:var(--muted)}
.news .read{margin-top:8px;width:206px;height:16px;background:var(--read);font-size:10.5px;color:var(--brand);padding-left:8px;line-height:16px}
.more-news{left:935px;top:793px;font-size:10.5px;color:var(--brand)}
.best-h{left:761px;top:826px;font-size:16.5px}
.best-panel{left:757px;top:859px;width:278px;height:228px;background:var(--panel)}
.best-thumb{width:112px;height:95px;border:1px solid #7fb1da}

/* footer */
.footer{left:0;top:1095px;width:1061px;height:105px;background:var(--footer);color:var(--white)}
.foot-links{left:24px;top:19px;display:flex;font-size:12px;list-style:none}
.foot-links li{padding:0 17px;border-left:1px solid rgba(255,255,255,.6)}
.foot-links li:first-child{padding-left:0;border-left:none}
.connect{left:826px;top:16px;display:flex;align-items:center;gap:8px;font-size:12px}
.connect .label{margin-right:8px}
.connect .social{width:20px;height:20px;border-radius:2px}
.copyright{left:24px;top:62px;font-size:11.5px}
</style>
</head>
<body>

<header class="abs hero" role="img" aria-label="Sky with clouds over the Dead Sea"></header>
<div class="abs hero-rule"></div>

<div class="abs logo">KELVORA®</div>

<div class="abs lang-label">Select Language</div>
<div class="abs lang" style="left:849px">EN</div>
<div class="abs lang" style="left:893px">DE</div>
<div class="abs lang" style="left:938px">ES</div>

<div class="abs social-box">
  <span class="social s-a" aria-label="Social network page"></span>
  <span class="social s-b" aria-label="Short message feed"></span>
  <span class="social s-c" aria-label="Video channel"></span>
  <span class="social s-rss" aria-label="News feed"></span>
</div>

<ul class="abs nav">
  <li class="active" style="width:88px">Main</li>
  <li style="width:106px">About Us</li>
  <li style="width:95px">Sitemap</li>
  <li style="width:106px">Products</li>
  <li style="width:91px">Links</li>
  <li style="width:189px;justify-content:flex-start;padding-left:23px">Contact Us</li>
</ul>

<div class="abs slider-frame"></div>
<section class="abs slider">
  <h1 class="abs slide-title"><b>Your Product</b> <span>Goes here..</span></h1>
  <p class="abs slide-copy">Brightwave Studio is a professional website design company dedicated to provide excellent services. We at Brightwave Studio think graphic design as a combination and collaboration of ideas and technology.</p>
  <div class="abs slide-btn">VIEW MORE PRODUCTS</div>
  <div class="abs dots">
    <span class="dot on">1</span><span class="dot">2</span><span class="dot">3</span><span class="dot">4</span>
  </div>
  <svg class="abs slide-photo" viewBox="0 0 456 311" role="img" aria-label="Photo of a bar of natural soap in a glass bowl with dried flowers">
    <defs>
      <linearGradient id="soap" x1="0" y1="0" x2="1" y2="1">
        <stop offset="0" stop-color="#b9b6ae"/>
        <stop offset=".45" stop-color="#d9b56a"/>
        <stop offset="1" stop-color="#8a6a4e"/>
      </linearGradient>
    </defs>
    <path d="M60 0 H456 V311 H40 Q-10 150 60 0 Z" fill="#3f86c6"/>
    <path d="M66 0 H456 V305 H48 Q2 150 66 0 Z" fill="url(#soap)"/>
  </svg>
  <div class="abs slide-arrow">
    <svg width="14" height="14" viewBox="0 0 14 14"><path d="M5 2 L10 7 L5 12" fill="none" stroke="#1a63ad" stroke-width="2.4" stroke-linecap="round" stroke-linejoin="round"/></svg>
  </div>
</section>

<h2 class="abs h2 welcome-h">Welcome to KELVORA NATURPRODUKTE WEBSITE</h2>
<div class="abs welcome-copy">
  <p>Brightwave Studio is a web service company, offering a wide range of services which range from designing and development, that is covering almost all the fields in the best possible way. To be the best we know what and how to present beautifully the working of the client’s need and their advantages be highlighted.</p>
  <p>We act in accordance with the Industry certified processes to deliver the best to our clients all over the world. Over years we have built a strong reputation in providing website design and web development services.</p>
  <p class="tight">E-Commerce is a major progress in technology that has changed the way in which the customers now purchase information, products and the services. It’s the new way of providing an opportunity to make your products and services available in the global market 24 hours a day through Internet</p>
</div>

<h2 class="abs h2 latest-h">Latest Products</h2>

<article class="abs card" style="left:22px">
  <div class="thumb" role="img" aria-label="Photo of a turquoise cream jar" style="background:linear-gradient(135deg,#7fd0d0,#2aa3a8 55%,#9fd9dc)"></div>
  <div class="name">Product Name</div>
  <p class="desc">Brightwave Studio is specialized in handling advanced web projects and the ongoing projects..</p>
  <div class="more">VIEW MORE</div>
</article>
<article class="abs card" style="left:268px">
  <div class="thumb" role="img" aria-label="Photo of pale natural soap bars" style="background:linear-gradient(135deg,#5a3a22,#e8d8b0 45%,#c9a878)"></div>
  <div class="name">Product Name</div>
  <p class="desc">Brightwave Studio is specialized in handling advanced web projects and the ongoing projects..</p>
  <div class="more">VIEW MORE</div>
</article>
<article class="abs card" style="left:509px">
  <div class="thumb" role="img" aria-label="Photo of a translucent glycerin soap on a dish" style="background:linear-gradient(135deg,#c9d2a8,#eed87a 50%,#b8b9a0)"></div>
  <div class="name">Product Name</div>
  <p class="desc">Brightwave Studio is specialized in handling advanced web projects and the ongoing projects..</p>
  <div class="more">VIEW MORE</div>
</article>

<h2 class="abs h2 news-h">Recent News &amp; Blogs</h2>
<div class="abs news" style="top:590px">
  <div class="date">20.Feb.2012</div>
  <p class="copy">Static website are the which are usually been used and are benefited through the Profes-sionals and Small Companies.</p>
  <div class="read">READ MORE</div>
</div>
<div class="abs news" style="top:692px">
  <div class="date">20.Feb.2012</div>
  <p class="copy">Static website are the which are usually been used and are benefited through the Profes-sionals and Small Companies.</p>
  <div class="read">READ MORE</div>
</div>
<div class="abs more-news">VIEW MORE NEWS</div>

<h2 class="abs h2 best-h">Some Best Natural Products</h2>
<div class="abs best-panel"></div>
<div class="abs best-thumb" style="left:774px;top:870px;background:linear-gradient(135deg,#5f7a4a,#d9d2c0 60%,#8f8fa8)" role="img" aria-label="Photo of soap with rosemary and lavender"></div>
<div class="abs best-thumb" style="left:898px;top:870px;background:linear-gradient(135deg,#8a7a3a,#bfa64e 50%,#d8d0b0)" role="img" aria-label="Photo of olive oil soap cubes"></div>
<div class="abs best-thumb" style="left:774px;top:977px;background:linear-gradient(135deg,#9a86c0,#d0c8d8 55%,#8f8aa0)" role="img" aria-label="Photo of lavender soap"></div>
<div class="abs best-thumb" style="left:901px;top:977px;background:linear-gradient(135deg,#e8e0d8,#f09a1a 50%,#c8a890)" role="img" aria-label="Photo of an orange slice with soap"></div>

<footer class="abs footer">
  <ul class="abs foot-links">
    <li>Home</li><li>About Us</li><li>Sitemap</li><li>Links</li><li>Contact Us</li><li>Download</li>
  </ul>
  <div class="abs connect">
    <span class="label">Connect With</span>
    <span class="social s-a" aria-label="Social network page"></span>
    <span class="social s-b" aria-label="Short message feed"></span>
    <span class="social s-c" aria-label="Video channel"></span>
    <span class="social s-rss" aria-label="News feed"></span>
  </div>
  <div class="abs copyright">Copyright © 2012 Company Name &nbsp;| &nbsp;All right reserved</div>
</footer>

</body>
</html>
```